New Business Card Design Project LORVANTI-Italy

we are LORVANTI-Italy
our company in the market for 3 years we are luxury cosmetic company and its about time for a facelift :)
i will like to have elegant luxurious and unique business card
that will give the person that get it a unique, luxurious and elegant impression
I'm VERY OPEN FOR NEW IDEAS , even duo i add a few files of things that i see on line and i like them

i add my logo as well
my website is LORVANTI.COM
(if you would like to see the main style that we have)

Target Market(s)

adult that have money :)

Industry/Entity Type

Business

Contact Information for Business Card

Name - Dario Lorvanti
Position - CEO and CO Founder
address - 4817 E Halvern
telephone - 555-384-1926
email - dario@lorvanti.com
fax - 555-384-1926
website - LORVANTI.COM

Colors
000000
959595
fbee3e
ffffff

Requirements
Must have
• big logo in GOLD color
• elegant look
• impressive
Nice to have
• not must but maybe classy pattern background
• not must but maybe emblem
• maybe clear plastic business card
Should not have
• colors
• images

```html
<!DOCTYPE html>
<html lang="en">
<head>
<meta charset="utf-8">
<title>LORVANTI Italy – Business Card</title>
<link rel="stylesheet" href="https://fonts.googleapis.com/css2?family=Cinzel:wght@500&family=Source+Sans+3:wght@400&display=swap">
<style>
  :root {
    --backdrop: #3a3331;
    --card-black: #0d0d0d;
    --card-edge: #1a1a1a;
    --silver: #c9c9c9;
    --gold: #e0b12c;
    --gold-soft: #c99a22;
  }
  * { margin: 0; padding: 0; box-sizing: border-box; }
  html, body {
    width: 1200px; height: 864px; overflow: hidden;
    background: var(--backdrop);
  }
  .canvas {
    width: 1200px; height: 864px;
    display: flex; align-items: center; justify-content: center; gap: 40px;
  }
  .card {
    position: relative;
    width: 540px; height: 309px;
    background: var(--card-black);
    border: 1px solid var(--card-edge);
    box-shadow: 0 12px 30px rgba(0,0,0,0.45);
  }

  /* Front side */
  .card-front {
    display: flex; flex-direction: column; align-items: center; justify-content: center;
  }
  .front-mark {
    width: 58px; height: 58px; border-radius: 50%;
    border: 2px solid var(--silver);
    margin-bottom: 18px;
  }
  .front-name {
    font-family: "Cinzel", serif; font-weight: 500;
    color: var(--silver);
    font-size: 40px; letter-spacing: 2px; line-height: 1;
  }
  .front-region {
    font-family: "Cinzel", serif; font-weight: 500;
    color: var(--silver);
    font-size: 14px; letter-spacing: 3px; margin-top: 10px;
  }

  /* Back side */
  .card-back { display: flex; align-items: center; padding-left: 46px; }
  .back-brand {
    width: 170px; display: flex; flex-direction: column; align-items: center;
  }
  .back-mark {
    width: 120px; height: 120px; border-radius: 50%;
    border: 3px solid var(--gold);
  }
  .back-brand-name {
    font-family: "Cinzel", serif; font-weight: 500;
    color: var(--gold); font-size: 18px; letter-spacing: 2px; margin-top: 12px;
  }
  .divider {
    width: 1px; height: 160px; margin: 0 22px 0 18px;
    background: linear-gradient(var(--card-black), var(--gold-soft) 30%, var(--gold-soft) 70%, var(--card-black));
  }
  .details { color: var(--gold); font-family: "Source Sans 3", sans-serif; }
  .person-name {
    font-family: "Cinzel", serif; font-weight: 500;
    font-size: 21px; letter-spacing: 1px; line-height: 1;
  }
  .person-role { font-size: 15px; margin-top: 2px; }
  .contact { list-style: none; font-size: 13px; line-height: 1.45; margin-top: 16px; }
  .website { font-size: 14px; margin-top: 14px; letter-spacing: 0.3px; }
</style>
</head>
<body>
<main class="canvas">
  <section class="card card-front" aria-label="Card front">
    <div class="front-mark"></div>
    <div class="front-name">LORVANTI</div>
    <div class="front-region">ITALY</div>
  </section>

  <section class="card card-back" aria-label="Card back">
    <div class="back-brand">
      <div class="back-mark"></div>
      <div class="back-brand-name">LORVANTI</div>
    </div>
    <div class="divider"></div>
    <div class="details">
      <div class="person-name">DARIO LORVANTI</div>
      <div class="person-role">CEO &amp; CO Founder</div>
      <ul class="contact">
        <li>4817 E Halvern</li>
        <li>P : 555-384-1926</li>
        <li>F : 555-384-1926</li>
        <li>E : dario@lorvanti.com</li>
      </ul>
      <div class="website">WWW.LORVANTI.COM</div>
    </div>
  </section>
</main>
</body>
</html>
```